Stationery Design Project

We need a stationery design for our Norwegian trucking company. We have existed for about 15 years and our 12 drivers uses relatively new vehicles to transport goods around in northern Norway. Long distance routes with fresh fish og food transport is our main operations.

We have already made alogo that's printed on our trucks. The logo and a picture of our trucks is attached. I think the logo i crappy, but since its already in use, changing it is not an option in this round. Still using a better colour scheme in the overall stationery and more interesting fonts is possible (altso in the logo).

Company details:
Name: Kjelvraket AS
Organisation nr 873 615 309
Post adress: 8642 Raudvik

I like minimalism and simplicity. I am avalibly for questions in normal GMT working hours either here or on mail: ivar@fjordlast.no

Reason: Hi. Im extending the deadline because I needed some time to find a vector file of our logo. Sorry for the inconvenience

Hi, and thanks for all your interest in the project. Some updates:

-          I have decided to commit to using one of the designs. Some designer will get the payment.

-          I have extended the deadline with 24 hours since I needed some time to find our firms vector logo (a slow Swedish man was holding me up)

-          We will not choose a design before the deadline. No need to rush.

-          We have received a lot of great design and think there is a need to specified the product we want to make:

o   Business Card for all our employers. I just need the design and will duplicate with the correct numbers and name myself. The information on should be: Logo, employer’s name, Phone number, email, website, Postal number and address. Use this as a template: logo, Leif Brattvoll, 47382066, Leif@fjordlast.no,, fjordlast.no, 8642 Raudvik. The order and placement of the information is your creative decision.

o   Stickers to put on the goods we travel. On the sticker the should be the following information: Logo, phone number, Tekst and link: Fraktæ av Kjelvraket. Ke du syns? Fjordlast.no/tilbakemelding (this means: Handled by Kjelvraket. What do you think Fjordlast.no/feedback -à the link will be a feedback form). The placement the information and size is your creative decision with some stings: we have been thinking of using Drukko for printing and see that a size about 6x6 cm, 8x5 or something like that. (with 3000 copies our budget is 200 punds). Any suggestions of other suppliers are welcome. Drukko price calculator http://www.drukkolabelhouse.co.uk/digital-litho-printing/printing-labels-tags/stickers/

o   Letterhead with logo, address, phone number and organizational number.

o   Envelopes with logo,address, phone number and organizational number.

Have a nice day.

 

 

• Using the blue colour in the logo and using a similar graphic approch.

```html
<!DOCTYPE html>
<html lang="no">
<head>
<meta charset="utf-8">
<title>Kjelvraket – visittkort</title>
<link rel="stylesheet" href="https://fonts.googleapis.com/css2?family=Open+Sans:wght@400;600;700&display=swap">
<style>
  :root {
    --backdrop-light: #c9cbce;
    --backdrop-dark: #6f7277;
    --white: #ffffff;
    --brand-blue: #0071bc;
    --deep-blue: #0d4fa3;
    --name-blue: #1a55a6;
    --text-dark: #2b2b2b;
    --divider: #b9b9b9;
  }
  * { margin: 0; padding: 0; box-sizing: border-box; }
  html, body { width: 1200px; height: 732px; overflow: hidden; }
  body {
    position: relative;
    font-family: "Open Sans", sans-serif;
    background: linear-gradient(160deg, var(--backdrop-light) 0%, var(--backdrop-dark) 45%, var(--backdrop-light) 70%, var(--backdrop-dark) 100%);
  }
  .card {
    position: absolute;
    width: 519px;
    height: 296px;
    overflow: hidden;
  }
  .card--front { left: 64px; top: 43px; background: var(--white); }
  .card--back-white { left: 617px; top: 43px; background: var(--white); border: 1px solid #8a8a8a; }
  .card--back-blue { left: 64px; top: 386px; background: var(--brand-blue); }
  .card--back-deep { left: 617px; top: 382px; background: var(--deep-blue); }

  .brand {
    position: absolute;
    display: flex;
    align-items: center;
    gap: 14px;
    font-weight: 700;
    font-size: 50px;
    letter-spacing: -0.5px;
    line-height: 1;
  }
  .brand__dot { width: 26px; height: 26px; border-radius: 50%; background: currentColor; }
  .card--front .brand { left: 88px; top: 50px; color: var(--brand-blue); }
  .card--back-white .brand { left: 88px; top: 108px; color: var(--brand-blue); }
  .card--back-blue .brand, .card--back-deep .brand { left: 88px; top: 108px; color: var(--white); }

  .web-line {
    position: absolute;
    left: 0; right: 0;
    top: 248px;
    text-align: center;
    font-size: 17px;
    letter-spacing: 3.2px;
  }
  .card--back-white .web-line { color: var(--text-dark); }
  .card--back-blue .web-line, .card--back-deep .web-line { color: var(--white); }
  .card--back-deep .web-line { top: 253px; }

  .contact {
    position: absolute;
    top: 164px;
    font-size: 14px;
    line-height: 21px;
    color: var(--text-dark);
  }
  .contact--person { right: calc(519px - 240px); text-align: right; }
  .contact--company { left: 262px; }
  .contact__name { color: var(--name-blue); font-weight: 700; font-size: 16.5px; }
  .contact__org { color: var(--name-blue); }
  .contact__row { display: flex; align-items: center; gap: 5px; }
  .contact--person .contact__row { justify-content: flex-end; }
  .contact__icon { width: 10px; height: 10px; fill: var(--name-blue); }
  .contact-divider {
    position: absolute;
    left: 252px; top: 164px;
    width: 1px; height: 66px;
    background: var(--divider);
  }
  .wave { position: absolute; left: 0; bottom: 0; width: 519px; height: 62px; }
</style>
</head>
<body>

<section class="card card--front">
  <div class="brand"><span class="brand__dot"></span>Kjelvraket</div>

  <div class="contact contact--person">
    <div class="contact__name">Leif Brattvoll</div>
    <div class="contact__row">
      <svg class="contact__icon" viewBox="0 0 10 10"><path d="M5 1 L10 5 H8.5 V10 H1.5 V5 H0 Z"/></svg>8642 Raudvik
    </div>
    <div class="contact__row">
      <svg class="contact__icon" viewBox="0 0 10 10"><path d="M2 0 L4 2.5 L3 4 Q4.5 6.5 6 7 L7.5 6 L10 8 L8.5 10 Q2 9 0 1.5 Z"/></svg>47382066
    </div>
  </div>

  <div class="contact-divider"></div>

  <div class="contact contact--company">
    <div class="contact__org">Org nr 873 615 309</div>
    <div class="contact__row">
      <svg class="contact__icon" viewBox="0 0 10 10"><path d="M0 3 L5 0 L10 3 V10 H0 Z M1 3.5 L5 6.5 L9 3.5"/></svg>Leif@fjordlast.no
    </div>
    <div class="contact__row">
      <svg class="contact__icon" viewBox="0 0 10 10"><circle cx="5" cy="5" r="4.5" fill="none" stroke="currentColor" style="stroke: var(--name-blue)"/><path d="M0.5 5 H9.5 M5 0.5 V9.5" stroke="#1a55a6" stroke-width="0.8"/></svg>www.fjordlast.no
    </div>
  </div>

  <svg class="wave" viewBox="0 0 519 62" preserveAspectRatio="none">
    <path d="M0 32 Q130 8 260 20 T519 0 V62 H0 Z" fill="var(--brand-blue)"/>
    <path d="M0 40 Q140 18 270 30 T519 6" fill="none" stroke="var(--white)" stroke-width="3"/>
    <path d="M0 44 Q150 24 280 36 T519 10 V62 H0 Z" fill="var(--deep-blue)"/>
  </svg>
</section>

<section class="card card--back-white">
  <div class="brand"><span class="brand__dot"></span>Kjelvraket</div>
  <p class="web-line">www.fjordlast.no</p>
</section>

<section class="card card--back-blue">
  <div class="brand"><span class="brand__dot"></span>Kjelvraket</div>
  <p class="web-line">www.fjordlast.no</p>
</section>

<section class="card card--back-deep">
  <div class="brand"><span class="brand__dot"></span>Kjelvraket</div>
  <p class="web-line">www.fjordlast.no</p>
</section>

</body>
</html>
```